VENTURE CAPITAL GROUP BUSINESS CARD DESIGN

Venture Capital Group based in SF looking for a bold business card design. No trendy colour explosion, 3D effects etc. Just "simple" optical effects. Works on your brain, keeps your eye focused and sticks to your mind.
Target Market(s)
Technology startups
Industry/Entity Type
Venture Capital
Contact Information for Business Card
DESMOND WHITLAKE
MANAGING PARTNER
187 FENWORTH ST SAN FRANCISCO, CA 94187
415.555.0142 O
415.555.0147 F
415.555.0193 C
desmond@veldtmoorcapital.ventures

```html
<!DOCTYPE html>
<html lang="en">
<head>
<meta charset="utf-8">
<title>Veldtmoor Capital Group – Business Card</title>
<link href="https://fonts.googleapis.com/css2?family=Open+Sans:wght@400;600;700&display=swap" rel="stylesheet">
<style>
  :root {
    --bg: #e9e9e7;
    --paper: #ffffff;
    --green: #2a8a2e;
    --green-light: #4fb04a;
    --green-dark: #0f5a17;
    --ink: #2b2b2b;
    --rule: #d6d6d6;
    --circle-grey: #e4e4e4;
  }
  * { margin: 0; padding: 0; box-sizing: border-box; }
  html, body { width: 1200px; height: 844px; overflow: hidden; }
  body {
    background: var(--bg);
    font-family: "Open Sans", Arial, sans-serif;
    position: relative;
  }
  .card {
    position: absolute;
    top: 272px;
    width: 520px;
    height: 300px;
    box-shadow: 0 6px 18px rgba(0,0,0,0.18);
  }
  /* Front */
  .card-front { left: 50px; background: var(--paper); }
  .front-brand {
    position: absolute; left: 0; top: 0; width: 250px; height: 100%;
    display: flex; flex-direction: column; align-items: center; justify-content: center;
  }
  .brand-circle {
    width: 86px; height: 86px; border-radius: 50%;
    background: radial-gradient(circle at 40% 35%, #ffffff, var(--circle-grey));
    margin-bottom: 14px;
  }
  .brand-name {
    font-weight: 600; color: var(--green);
    font-size: 24px; letter-spacing: 1px; line-height: 1.1; text-align: center;
  }
  .brand-sub {
    font-weight: 600; color: var(--green);
    font-size: 9px; letter-spacing: 4px; margin-top: 4px;
  }
  .front-divider {
    position: absolute; left: 250px; top: 40px; bottom: 40px; width: 1px;
    background: linear-gradient(var(--paper), var(--rule), var(--paper));
  }
  .front-details {
    position: absolute; left: 272px; top: 42px; right: 16px;
    color: var(--ink); font-size: 12.5px; line-height: 1.35;
  }
  .person-name { color: var(--green); font-weight: 700; font-size: 17px; line-height: 1.2; }
  .person-title { font-size: 12.5px; margin-bottom: 16px; }
  .address { margin-bottom: 14px; }
  .contact-list { list-style: none; }
  .contact-list li { display: flex; align-items: center; gap: 7px; margin-bottom: 2px; }
  .contact-list svg { width: 10px; height: 10px; fill: var(--green); flex-shrink: 0; }
  /* Back */
  .card-back {
    left: 630px;
    background: linear-gradient(135deg, var(--green-light) 0%, var(--green) 50%, var(--green-dark) 100%);
    display: flex; flex-direction: column; align-items: center; justify-content: center;
    color: #ffffff;
  }
  .card-back .brand-circle { background: #ffffff; width: 92px; height: 92px; }
  .card-back .brand-name, .card-back .brand-sub { color: #ffffff; }
</style>
</head>
<body>
  <section class="card card-front">
    <div class="front-brand">
      <div class="brand-circle"></div>
      <div class="brand-name">VELDTMOOR</div>
      <div class="brand-sub">CAPITAL GROUP</div>
    </div>
    <div class="front-divider"></div>
    <div class="front-details">
      <div class="person-name">Desmond Whitlake</div>
      <div class="person-title">Managing Partner</div>
      <div class="address">187 Fenworth St San<br>Francisco, CA 94187</div>
      <ul class="contact-list">
        <li><svg viewBox="0 0 10 10"><path d="M2 0.5l2 2-1 1.2c.6 1.3 1.6 2.3 2.8 2.8L7 5.5l2 2-1.3 1.8C4 9 1 6 .7 2.3z"/></svg>415.555.0142</li>
        <li><svg viewBox="0 0 10 10"><path d="M2 0h6v3H2zM0 3.5h10V9H0zM2 6h6v3H2z"/></svg>415.555.0147</li>
        <li><svg viewBox="0 0 10 10"><path d="M2.5 0h5v10h-5zM3.3 1v7h3.4V1z"/></svg>415.555.0193</li>
        <li><svg viewBox="0 0 10 10"><path d="M0 1.5h10v7H0zM.8 2.3L5 5.6l4.2-3.3z"/></svg>desmond@veldtmoorcapital.ventures</li>
      </ul>
    </div>
  </section>

  <section class="card card-back">
    <div class="brand-circle"></div>
    <div class="brand-name">VELDTMOOR</div>
    <div class="brand-sub">CAPITAL GROUP</div>
  </section>
</body>
</html>
```